RM Installations Web Site Design

Need a basic site to show clients a little about what we do. We are a custom audio video company in the high-end residential market. Need a few basic but professional pages to show past projects and products we sell. No e-commerce. Should include my new logo from MarkBazaar.

Industry/Entity Type

Residential

Number of Pages Required

2 page

Font styles to use
Serif
Sans Serif

Colors
f78f20

Requirements
Must have
• Company Logo, Send feedback page
Nice to have
• I have no ideas about design, but I do know what I like and dislike when I see it.

```html
<!DOCTYPE html>
<html lang="en">
<head>
<meta charset="utf-8">
<title>RM Installations</title>
<link href="https://fonts.googleapis.com/css2?family=Oswald:wght@400;500&family=Lato:wght@400;700&display=swap" rel="stylesheet">
<style>
:root{
  --orange:#f78f20;
  --orange-dark:#e07a10;
  --ink:#1b1b1b;
  --dark:#1e1e1e;
  --darker:#121212;
  --text:#5a5a5a;
  --grey-1:#ebebea;
  --grey-2:#f3f3f2;
  --white:#ffffff;
}
*{box-sizing:border-box;margin:0;padding:0}
html,body{width:1200px;height:2236px;overflow:hidden}
body{position:relative;font-family:'Lato',sans-serif;color:var(--text);background:var(--white)}
.abs{position:absolute}
.topbar{left:0;top:0;width:1200px;height:100px;background:linear-gradient(90deg,#f29a2a,#f7a43a 50%,#f08f1e)}
.brand{left:131px;top:30px;display:flex;align-items:center;gap:10px;font-family:'Oswald',sans-serif;font-weight:500;font-size:24px;color:var(--ink);text-transform:uppercase}
.brand .mark{width:30px;height:30px;background:var(--ink)}
.contact-top{top:28px;display:flex;align-items:center;gap:14px;color:var(--white)}
.contact-top .ico{width:40px;height:40px}
.contact-top small{display:block;font-size:12px}
.contact-top span{font-size:18px}
.nav{left:0;top:100px;width:1200px;height:48px;background:var(--ink);border-top:2px solid #333;display:flex;padding-left:131px;font-size:15px;color:#c8c8c8;align-items:center}
.nav a{color:inherit;text-decoration:none;padding:0 24px;border-right:1px solid #555;line-height:14px}
.nav a:last-child{border:0}
.nav a.active{background:var(--orange);color:var(--white);line-height:46px;border:0;padding:0 25px;margin-right:2px}
.hero{left:0;top:148px;width:1200px;height:452px;background:radial-gradient(ellipse at 50% 30%,#f6a445,#e37a1c 70%),#e8841f}
.hero-caption{left:0;top:508px;width:1200px;height:92px;background:rgba(38,38,38,.9)}
.hero-caption .split{left:430px;top:0;width:3px;height:92px;background:#777;transform:skewX(-18deg)}
.welcome{left:133px;top:16px;font-family:'Oswald',sans-serif;font-size:28px;line-height:32px;color:var(--white)}
.welcome b{display:block;color:var(--orange);font-weight:500}
.tagline{left:478px;top:20px;width:620px;font-size:19px;line-height:27px;color:var(--white)}
.arrow{width:34px;height:34px;background:#2a2a2a;display:flex;align-items:center;justify-content:center}
.arrow.grey{background:#c2c2c2}
.title{left:0;width:1200px;text-align:center;font-family:'Oswald',sans-serif;font-weight:500;font-size:31px;color:var(--ink);text-transform:uppercase}
.title em{font-style:normal;color:var(--orange)}
.card{width:216px;top:702px;height:280px}
.card .pic{height:160px}
.card .body{height:120px;background:var(--orange);padding:20px 11px 0;color:var(--white)}
.card h3{font-family:'Oswald',sans-serif;font-weight:400;font-size:17px}
.card p{font-size:13px;line-height:19px;color:#fde6cc;margin-top:10px}
.card .more{font-size:11px;margin-top:8px;display:block;color:#2a2a2a}
.about{left:0;top:1020px;width:612px;height:366px;background:var(--grey-1)}
.team{left:612px;top:1020px;width:588px;height:366px;background:var(--grey-2)}
.sec-h{font-family:'Oswald',sans-serif;font-weight:500;font-size:30px;color:var(--ink);text-transform:uppercase}
.sec-h em{font-style:normal;color:var(--orange)}
.about p{font-size:13px;line-height:19.5px;margin-top:16px}
.btn{display:inline-block;background:var(--orange);color:var(--ink);font-size:11px;padding:9px 15px;border-bottom:3px solid #b85f0c;border-radius:2px}
.member{display:flex;gap:18px;margin-top:28px}
.member .face{width:92px;height:92px;flex:none}
.member h4{font-family:'Oswald',sans-serif;font-weight:500;font-size:17px;color:var(--orange)}
.member small{font-style:italic;font-size:12px}
.member p{font-size:13px;line-height:19px;margin-top:6px}
.proj{top:1488px;width:216px}
.proj .pic{height:160px}
.proj h3{font-family:'Oswald',sans-serif;font-weight:400;font-size:17px;color:var(--orange);margin-top:12px}
.contact{left:0;top:1705px;width:1200px;height:483px;background:var(--dark);color:#d8d8d8}
.col-h{font-family:'Oswald',sans-serif;font-size:17px;color:var(--white)}
.field{width:382px;height:42px;background:var(--white);border-radius:3px;color:#777;font-size:14px;padding:12px 14px}
.submit{width:118px;height:40px;background:var(--orange);color:var(--white);font-family:'Oswald',sans-serif;font-size:19px;text-align:center;line-height:40px}
.drow{display:flex;align-items:center;gap:12px;font-size:15px;color:var(--white)}
.drow svg{flex:none}
.social{display:flex;align-items:center;gap:16px;font-size:13px;color:#cfcfcf;margin-bottom:14px}
.footer{left:0;top:2188px;width:1200px;height:48px;background:var(--darker);color:#bbb;font-size:13px;text-align:center;line-height:48px}
</style>
</head>
<body>

<header>
  <div class="abs topbar"></div>
  <div class="abs brand"><span class="mark"></span>RM Installations</div>
  <div class="abs contact-top" style="left:663px">
    <svg class="ico" viewBox="0 0 40 40"><rect x="6" y="6" width="28" height="28" rx="4" transform="rotate(45 20 20)" fill="#2a1d10"/><path d="M15 14l3 0 1 4-2 1c1 2 3 4 5 5l1-2 4 1 0 3c-6 0-12-6-12-12z" fill="#f78f20"/></svg>
    <div><small>Call Us</small><span>(555)-210-48397</span></div>
  </div>
  <div class="abs contact-top" style="left:888px">
    <svg class="ico" viewBox="0 0 40 40"><rect x="6" y="6" width="28" height="28" rx="4" transform="rotate(45 20 20)" fill="#2a1d10"/><rect x="13" y="15" width="14" height="10" fill="#f78f20"/><path d="M13 15l7 6 7-6" stroke="#2a1d10" stroke-width="1.5" fill="none"/></svg>
    <div><small>Email Us</small><span>info@rminstall.net</span></div>
  </div>
  <nav class="abs nav">
    <a class="active">HOME</a><a>OUR TEAM</a><a>PRODUCTS</a><a>OUR SERVICES</a><a>PAST PROJECT</a><a>FEEDBACK</a><a>CONTACT US</a>
  </nav>
</header>

<section>
  <div class="abs hero" role="img" aria-label="Home cinema room with orange wall, wall-mounted screen, speakers and red lounge chairs"></div>
  <div class="abs arrow" style="left:8px;top:345px"><svg width="12" height="12" viewBox="0 0 12 12"><path d="M8 1L3 6l5 5" stroke="#fff" stroke-width="2.5" fill="none"/></svg></div>
  <div class="abs arrow" style="left:1158px;top:345px"><svg width="12" height="12" viewBox="0 0 12 12"><path d="M4 1l5 5-5 5" stroke="#fff" stroke-width="2.5" fill="none"/></svg></div>
  <div class="abs hero-caption">
    <div class="abs split"></div>
    <div class="abs welcome">Welcom to<b>RM Installations</b></div>
    <div class="abs tagline">We expert in Residential Cinemas Make your Home Safe &amp; Secure With our largest audio video control system</div>
  </div>
</section>

<section>
  <h2 class="abs title" style="top:638px"><em>Our</em> Services</h2>
  <div class="abs arrow grey" style="left:94px;top:824px"><svg width="12" height="12" viewBox="0 0 12 12"><path d="M8 1L3 6l5 5" stroke="#fff" stroke-width="2.5" fill="none"/></svg></div>
  <div class="abs arrow grey" style="left:1072px;top:824px"><svg width="12" height="12" viewBox="0 0 12 12"><path d="M4 1l5 5-5 5" stroke="#fff" stroke-width="2.5" fill="none"/></svg></div>
  <div class="abs card" style="left:131px"><div class="pic" role="img" aria-label="Dark red home theatre with recliners" style="background:linear-gradient(#4a1a1c,#2a0f10)"></div><div class="body"><h3>Residential Cinemas</h3><p>Lor ipsumdolorsitac nsectetur adipiscing elit d.uis.</p><span class="more">View Details »</span></div></div>
  <div class="abs card" style="left:371px"><div class="pic" role="img" aria-label="Couple reviewing a design on a laptop" style="background:linear-gradient(#d9c8b4,#9a7d62)"></div><div class="body"><h3>Design And Consultations</h3><p>Lor ipsumdolorsitac nsectetur adipiscing elit d.uis.</p><span class="more">View Details »</span></div></div>
  <div class="abs card" style="left:612px"><div class="pic" role="img" aria-label="Hand holding a remote in a living room" style="background:linear-gradient(#8a5a44,#3d2a22)"></div><div class="body"><h3>Automated Lighting Control</h3><p>Lor ipsumdolorsitac nsectetur adipiscing elit d.uis.</p><span class="more">View Details »</span></div></div>
  <div class="abs card" style="left:853px"><div class="pic" role="img" aria-label="Outdoor stone wall with mounted television" style="background:linear-gradient(#8f8676,#5b5247)"></div><div class="body"><h3>Outdoor Audio and Video</h3><p>Lor ipsumdolorsitac nsectetur adipiscing elit d.uis.</p><span class="more">View Details »</span></div></div>
</section>

<section class="abs about">
  <div class="abs" style="left:131px;top:36px;width:446px">
    <h2 class="sec-h"><em>About</em> <span style="font-size:18px;color:var(--ink)">RM Installations</span></h2>
    <p>Lorem ipsum dolor sit amet, consectetuer adipiscing elit, sed diam nonummy nibh euismod tincidunt ut laoreet dolore magna aliquam erat volutpat. Ut wisi enim ad minim veniam, quis nostrud exerci tation ullamcorper suscipit lobortis nisl ut aliquip ex ea commodo consequat.</p>
    <p>Duis autem vel eum iriure dolor in hendrerit in vulputate velit esse molestie consequat, vel illum dolore eu feugiat nulla facilisis at vero eros et accumsan et iusto odio dignissim qui blandit praesent luptatum zzril delenit augue duis dolore te feugait nulla facilisi.</p>
    <div style="margin-top:16px"><span class="btn">Read More »</span></div>
  </div>
</section>
<section class="abs team">
  <div class="abs" style="left:44px;top:36px;width:420px">
    <h2 class="sec-h"><em>Our</em> Team</h2>
    <div class="member">
      <svg class="face" viewBox="0 0 92 92" role="img" aria-label="Portrait of team director"><rect x="16" y="16" width="60" height="60" rx="12" transform="rotate(45 46 46)" fill="#c9c3bb"/></svg>
      <div><h4>Dan Porter</h4><small>Director</small><p>Ut wisi enim ad minim veniam, quis nostrud exerci tation ullamcorper suscipit lobortis nisl ut aliquip.</p></div>
    </div>
    <div class="member" style="margin-top:24px">
      <svg class="face" viewBox="0 0 92 92" role="img" aria-label="Portrait of team director"><rect x="16" y="16" width="60" height="60" rx="12" transform="rotate(45 46 46)" fill="#bdb4ab"/></svg>
      <div><h4>Lena Hart</h4><small>Director</small><p>Ut wisi enim ad minim veniam, quis nostrud exerci tation ullamcorper suscipit lobortis nisl ut aliquip.</p></div>
    </div>
  </div>
</section>

<section>
  <h2 class="abs title" style="top:1426px"><em>Past</em> Project</h2>
  <div class="abs arrow grey" style="left:94px;top:1550px"><svg width="12" height="12" viewBox="0 0 12 12"><path d="M8 1L3 6l5 5" stroke="#fff" stroke-width="2.5" fill="none"/></svg></div>
  <div class="abs arrow grey" style="left:1072px;top:1550px"><svg width="12" height="12" viewBox="0 0 12 12"><path d="M4 1l5 5-5 5" stroke="#fff" stroke-width="2.5" fill="none"/></svg></div>
  <div class="abs proj" style="left:131px"><div class="pic" role="img" aria-label="Media room with sofa and large screen" style="background:linear-gradient(#5a3a2a,#2b1a14)"></div><h3>Residential Cinemas</h3></div>
  <div class="abs proj" style="left:371px"><div class="pic" role="img" aria-label="Office desk with multiple monitors" style="background:linear-gradient(#6a6a6a,#2e2e2e)"></div><h3>Design And Consultations</h3></div>
  <div class="abs proj" style="left:612px"><div class="pic" role="img" aria-label="Orange room with screen, speakers and red chairs" style="background:linear-gradient(#f3a244,#e07c1e)"></div><h3>Automated Lighting Control</h3></div>
  <div class="abs proj" style="left:853px"><div class="pic" role="img" aria-label="Living room with fireplace, TV and tablet" style="background:linear-gradient(#d9d6d0,#6e665c)"></div><h3>Outdoor Audio and Video</h3></div>
</section>

<footer>
  <section class="abs contact">
    <h2 class="abs title" style="top:40px;color:var(--orange)">Contact <span style="color:#bbb">Us</span></h2>
    <div class="abs" style="left:131px;top:112px">
      <div class="col-h">FeedBack</div>
      <div class="field" style="margin-top:18px">Name</div>
      <div class="field" style="margin-top:14px">Email</div>
      <div class="field" style="margin-top:14px">Phone</div>
      <div class="field" style="margin-top:14px;height:80px">Message</div>
      <div class="submit" style="margin-top:14px">SUBMIT</div>
    </div>
    <div class="abs" style="left:560px;top:112px;width:310px">
      <div class="col-h">Contact Detail</div>
      <div class="drow" style="margin-top:18px;align-items:flex-start;font-size:13px;line-height:19px;color:#ddd">
        <svg width="50" height="50" viewBox="0 0 50 50"><rect x="10" y="10" width="30" height="30" rx="5" transform="rotate(45 25 25)" fill="#f78f20"/><path d="M25 16a6 6 0 0 1 6 6c0 5-6 12-6 12s-6-7-6-12a6 6 0 0 1 6-6z" fill="#fff"/><circle cx="25" cy="22" r="2" fill="#f78f20"/></svg>
        <span>Lorem ipsum dolor sit amet, consectetuer adipiscing elit, sed diam nonummy nibh euismod.</span>
      </div>
      <div class="drow" style="margin-top:16px"><svg width="50" height="50" viewBox="0 0 50 50"><rect x="10" y="10" width="30" height="30" rx="5" transform="rotate(45 25 25)" fill="#f78f20"/><path d="M19 18l4 0 1 4-2 1c1 2 3 4 5 5l1-2 4 1 0 4c-7 0-13-6-13-13z" fill="#fff"/></svg>(555)-210-48397</div>
      <div class="drow" style="margin-top:12px"><svg width="50" height="50" viewBox="0 0 50 50"><rect x="10" y="10" width="30" height="30" rx="5" transform="rotate(45 25 25)" fill="#f78f20"/><rect x="18" y="21" width="14" height="11" fill="#fff"/><rect x="21" y="17" width="8" height="5" fill="none" stroke="#fff" stroke-width="2"/></svg>(555)-210-48397</div>
      <div class="drow" style="margin-top:12px"><svg width="50" height="50" viewBox="0 0 50 50"><rect x="10" y="10" width="30" height="30" rx="5" transform="rotate(45 25 25)" fill="#f78f20"/><rect x="18" y="20" width="14" height="10" fill="#fff"/><path d="M18 20l7 6 7-6" stroke="#f78f20" stroke-width="1.5" fill="none"/></svg>info@rminstall.net</div>
    </div>
    <div class="abs" style="left:916px;top:112px">
      <div class="col-h" style="margin-bottom:14px">Follow Us</div>
      <div class="social"><svg width="46" height="46" viewBox="0 0 46 46"><rect x="9" y="9" width="28" height="28" rx="4" transform="rotate(45 23 23)" fill="#1b5a8f"/></svg>FRIENDBOOK</div>
      <div class="social"><svg width="46" height="46" viewBox="0 0 46 46"><rect x="9" y="9" width="28" height="28" rx="4" transform="rotate(45 23 23)" fill="#1fa8cf"/></svg>CHIRPER</div>
      <div class="social"><svg width="46" height="46" viewBox="0 0 46 46"><rect x="9" y="9" width="28" height="28" rx="4" transform="rotate(45 23 23)" fill="#1a87b8"/></svg>WORKLINK</div>
      <div class="social"><svg width="46" height="46" viewBox="0 0 46 46"><rect x="9" y="9" width="28" height="28" rx="4" transform="rotate(45 23 23)" fill="#d9533f"/></svg>CIRCLES</div>
    </div>
  </section>
  <div class="abs footer">© 2015 RM Installations. All rights reserved.</div>
</footer>

</body>
</html>
```